Verdana Crest New Website - Online Learning and Education

New Wordpress website for an online learning site that has courses, worksheets, quizzes, etc.
Updates

We would like something similar to this website: https://hallowaybridgeinstitute.example/mediation-skills-course/. But continue with the content of our current website: http://verdanacrestlearninghub.example

We would like something similar to this site: https://hallowaybridgeinstitute.example/mediation-skills-course/

Coding

Coded - Design and coding required

```html
<!DOCTYPE html>
<html lang="en">
<head>
<meta charset="utf-8">
<title>Verdana Crest Learning System</title>
<link href="https://fonts.googleapis.com/css2?family=Poppins:wght@400;500&family=Open+Sans:wght@400;600&display=swap" rel="stylesheet">
<style>
:root{
  --navy:#164a86;
  --red:#c3202e;
  --text:#333;
  --sidebar-grey:#ececec;
  --footer:#262626;
  --teal:#3cc7a6;
}
*{box-sizing:border-box;margin:0;padding:0}
html,body{width:1200px;height:2189px;overflow:hidden;background:#fff}
body{position:relative;font-family:"Open Sans",sans-serif;color:var(--text)}
.site-header{position:absolute;left:0;top:0;width:1200px;height:72px;background:#fff}
.brand{position:absolute;left:144px;top:22px;display:flex;align-items:center;gap:8px;font-family:"Poppins",sans-serif;font-weight:500;font-size:22px;color:var(--navy)}
.brand-dot{width:22px;height:22px;border-radius:50%;background:var(--navy)}
.main-nav a{position:absolute;top:28px;font-family:"Poppins",sans-serif;font-size:13.5px;color:#555;text-decoration:none}
.main-nav a.active{color:#3b7dd8}
.btn{position:absolute;top:21px;height:32px;line-height:32px;text-align:center;font-family:"Poppins",sans-serif;font-size:13.5px;color:#fff;border-radius:2px}
.btn-login{left:903px;width:64px;background:var(--navy)}
.btn-register{left:975px;width:80px;background:var(--red)}
.hero{position:absolute;left:0;top:72px;width:1200px;height:440px;background:linear-gradient(90deg,#9aa889 0%,#eeede9 18%,#f5f3ef 45%,#e8dccf 62%,#c9a488 80%,#e9e6e2 100%)}
.hero-title{position:absolute;left:0;width:1200px;top:68px;text-align:center;font-family:"Poppins",sans-serif;font-weight:500;font-size:41px;line-height:52px;color:var(--navy)}
.hero-sub{position:absolute;left:0;width:1200px;top:125px;text-align:center;font-family:"Poppins",sans-serif;font-size:16px;line-height:22px;color:#333}
.hero-arrow{position:absolute;top:206px}
h2.section{position:absolute;left:144px;font-family:"Poppins",sans-serif;font-weight:500;font-size:34px;color:var(--red);line-height:1}
p.copy{position:absolute;left:144px;width:660px;font-size:12.4px;letter-spacing:-0.1px;line-height:22.5px;color:#444}
.topics{position:absolute;left:144px;top:780px;width:500px;list-style:none;font-size:15px;color:var(--navy)}
.topics li{position:absolute;white-space:nowrap}
.topics li::before{content:"›";margin-right:8px;color:var(--navy)}
.finder{position:absolute;left:824px;top:568px;width:232px;height:207px;background:linear-gradient(160deg,#c71e2c 0%,#8f2a4a 45%,#1c4a86 100%)}
.finder h3{position:absolute;left:0;width:232px;top:12px;text-align:center;font-family:"Poppins",sans-serif;font-weight:400;font-size:29px;color:#fff}
.field{position:absolute;left:8px;width:216px;height:40px;background:#fff;font-size:13.5px;color:#777;padding:10px 13px}
.field svg{position:absolute;right:14px;top:12px}
.search-btn{position:absolute;left:8px;top:157px;width:216px;height:41px;background:#222;color:#fff;text-align:center;line-height:41px;font-weight:600;font-size:15px}
.help{position:absolute;left:824px;top:784px;width:232px;height:159px;background:var(--sidebar-grey)}
.help h3{position:absolute;left:24px;top:14px;font-family:"Poppins",sans-serif;font-weight:500;font-size:28px;line-height:31px;color:var(--navy)}
.help p{position:absolute;left:24px;top:82px;width:178px;font-size:12px;line-height:19px;color:#444}
.screen{position:absolute;top:1184px;height:242px;background:#fff;box-shadow:0 1px 4px rgba(0,0,0,.25);overflow:hidden}
.video{position:absolute;left:144px;top:1458px;width:655px;height:351px;background:linear-gradient(120deg,#3e4a2e 0%,#4b4438 35%,#2f2b27 60%,#6e6a60 100%)}
.newsletter{position:absolute;left:0;top:1878px;width:1200px;height:191px;background:var(--navy)}
.newsletter h3{position:absolute;left:0;width:1200px;top:38px;text-align:center;font-family:"Poppins",sans-serif;font-weight:400;font-size:34px;color:#fff}
.email{position:absolute;left:400px;top:95px;width:399px;height:47px;background:#fff;padding:12px 22px;font-family:"Poppins",sans-serif;font-size:16px;color:#bbb}
.email svg{position:absolute;right:16px;top:16px}
.site-footer{position:absolute;left:0;top:2069px;width:1200px;height:120px;background:var(--footer)}
.footer-links{position:absolute;left:144px;top:37px;font-size:12px;color:#ccc}
.footer-links span{color:#888;margin:0 9px}
.copyright{position:absolute;left:144px;top:66px;font-size:12px;color:#ccc}
.social{position:absolute;top:64px;width:25px;height:25px;border-radius:50%}
</style>
</head>
<body>

<header class="site-header">
  <div class="brand"><span class="brand-dot"></span>Verdana Crest</div>
  <nav class="main-nav">
    <a class="active" style="left:491px">Courses</a>
    <a style="left:575px">Worksheets</a>
    <a style="left:681px">Quizzes</a>
    <a style="left:760px">Blog</a>
    <a style="left:818px">Support</a>
  </nav>
  <div class="btn btn-login">Login</div>
  <div class="btn btn-register">Register</div>
</header>

<section class="hero" role="img" aria-label="Photo of a woman relaxing on a tufted sofa working on a laptop, with a plant, floor lamp and sequined curtain">
  <div class="hero-title">Verdana Crest Learning System</div>
  <div class="hero-sub">Get Your Bearings. Plan Your Course.</div>
  <svg class="hero-arrow" style="left:54px" width="18" height="28" viewBox="0 0 18 28"><path d="M15 2 3 14l12 12" fill="none" stroke="#1d4f8c" stroke-width="3"/></svg>
  <svg class="hero-arrow" style="left:1127px" width="18" height="28" viewBox="0 0 18 28"><path d="M3 2l12 12L3 26" fill="none" stroke="#1d4f8c" stroke-width="3"/></svg>
</section>

<h2 class="section" style="top:564px">Welcome to Verdana Crest!</h2>
<p class="copy" style="top:606px">Verdana Crest, the Virtual Workplace Skills Hub, is an online learning application geared toward corporate customers, allowing their employees to identify and cultivate new skills that will be valuable in both their professional and personal lives. Named after a guiding high ridge, Verdana Crest can help your people get their bearings for where they’re headed, and then help them plan a course to get there.</p>
<p class="copy" style="top:718px">Concentrating on subjects that are useful to each student not only in the business world but also in life as well, Verdana Crest offers courses on various topics including:</p>

<ul class="topics">
  <li style="left:0;top:0">Become a Better Listener</li>
  <li style="left:0;top:32px">Proactive Decision-Making</li>
  <li style="left:0;top:64px">Improving Self-Awareness</li>
  <li style="left:0;top:96px">The Power of Priorities</li>
  <li style="left:238px;top:0">Mastering Habits</li>
  <li style="left:238px;top:32px">Managing a To-Do List</li>
  <li style="left:238px;top:64px">Perfection: The Enemy of Progress</li>
</ul>

<h2 class="section" style="top:932px">Different Learning Styles</h2>
<p class="copy" style="top:974px">Verdana Crest realizes that different people learn in different ways, so we strive to accommodate that. The courses within Verdana Crest include various methods of information dissemination to allow for different learning styles: some reading, some video, some reflections, some group activities, and some journaling. Each course includes a brief quiz to ensure you’ve absorbed the important information. And, if your organization chooses to work through these courses together as a group, that will further enhance your team’s learning experience.</p>

<h2 class="section" style="top:1129px">Sample Screens</h2>

<div class="screen" style="left:144px;width:311px">
  <svg width="311" height="242" viewBox="0 0 311 242" font-family="Open Sans, sans-serif">
    <rect width="311" height="14" fill="#e4e4e4"/>
    <circle cx="5" cy="6" r="2" fill="#e0574f"/><circle cx="11" cy="6" r="2" fill="#e5b13c"/><circle cx="17" cy="6" r="2" fill="#5cc058"/>
    <rect x="10" y="15" width="290" height="6" rx="2" fill="#f3f3f3"/>
    <line x1="0" y1="37" x2="311" y2="37" stroke="#ddd"/>
    <rect x="0" y="38" width="3" height="204" fill="#222"/>
    <text x="13" y="72" font-size="11" fill="#333">Focus</text>
    <text x="13" y="91" font-size="8" fill="#333">Overview</text>
    <rect x="15" y="102" width="184" height="106" fill="#b9b9b9" role="img" aria-label="Photo of a record player with a quote overlay"/>
    <rect x="228" y="48" width="70" height="5" fill="#ddd"/>
    <text x="228" y="75" font-size="5" fill="#333">Course Outline</text>
    <g fill="#ccc"><rect x="232" y="82" width="60" height="2"/><rect x="232" y="90" width="60" height="2"/><rect x="232" y="98" width="60" height="2"/><rect x="232" y="106" width="60" height="2"/><rect x="232" y="114" width="60" height="2"/><rect x="232" y="122" width="60" height="2"/><rect x="232" y="130" width="60" height="2"/><rect x="232" y="138" width="60" height="2"/><rect x="232" y="146" width="60" height="2"/><rect x="232" y="154" width="60" height="2"/><rect x="232" y="162" width="60" height="2"/></g>
    <rect x="242" y="212" width="46" height="9" fill="#5b6a86"/>
    <text x="249" y="219" font-size="5" fill="#fff">MY JOURNAL</text>
    <g fill="#999"><rect x="13" y="216" width="150" height="2"/><rect x="13" y="225" width="190" height="2"/><rect x="13" y="233" width="180" height="2"/></g>
  </svg>
</div>

<div class="screen" style="left:479px;width:312px">
  <svg width="312" height="242" viewBox="0 0 312 242" font-family="Open Sans, sans-serif">
    <rect width="312" height="14" fill="#e4e4e4"/>
    <circle cx="5" cy="6" r="2" fill="#e0574f"/><circle cx="11" cy="6" r="2" fill="#e5b13c"/><circle cx="17" cy="6" r="2" fill="#5cc058"/>
    <rect x="10" y="15" width="290" height="6" rx="2" fill="#f3f3f3"/>
    <line x1="0" y1="37" x2="312" y2="37" stroke="#ddd"/>
    <text x="14" y="44" font-size="5.5" fill="#333">1. Question</text>
    <g fill="#aaa"><rect x="14" y="57" width="170" height="2"/><rect x="14" y="65" width="40" height="2"/><rect x="20" y="80" width="30" height="2"/><rect x="20" y="87" width="30" height="2"/><rect x="20" y="94" width="60" height="2"/></g>
    <rect x="14" y="108" width="184" height="40" fill="#f4f6ee" stroke="#ddd"/>
    <rect x="14" y="140" width="184" height="7" fill="var(--teal)"/>
    <rect x="14" y="160" width="184" height="16" fill="#f4f4f4" stroke="#ddd"/>
    <text x="14" y="186" font-size="5.5" fill="#333">2. Question</text>
    <g fill="#aaa"><rect x="14" y="198" width="180" height="2"/><rect x="14" y="206" width="30" height="2"/></g>
    <rect x="14" y="223" width="184" height="7" fill="var(--teal)"/>
    <rect x="14" y="232" width="184" height="7" fill="var(--teal)"/>
    <g fill="#aaa"><rect x="232" y="40" width="50" height="2"/><rect x="232" y="48" width="55" height="2"/><rect x="232" y="56" width="40" height="2"/><rect x="232" y="64" width="45" height="2"/></g>
    <text x="226" y="91" font-size="5" fill="#333">My Journal</text>
    <rect x="240" y="112" width="46" height="9" fill="#4a4a4a"/>
    <text x="247" y="119" font-size="5" fill="#fff">MY JOURNAL</text>
  </svg>
</div>

<div class="video" role="img" aria-label="Video still of a man using a tablet and a laptop">
  <svg style="position:absolute;left:307px;top:155px" width="41" height="41" viewBox="0 0 41 41"><circle cx="20.5" cy="20.5" r="20" fill="#fff"/><path d="M15 11l14 9.5L15 30z" fill="#222"/></svg>
</div>

<aside class="finder">
  <h3>Find Topic</h3>
  <div class="field" style="top:62px">Search Topic
    <svg width="16" height="14" viewBox="0 0 16 14" fill="#555"><rect width="3" height="2"/><rect x="5" width="11" height="2"/><rect y="4" width="3" height="2"/><rect x="5" y="4" width="11" height="2"/><rect y="8" width="3" height="2"/><rect x="5" y="8" width="11" height="2"/><rect y="12" width="3" height="2"/><rect x="5" y="12" width="11" height="2"/></svg>
  </div>
  <div class="field" style="top:110px">Search Teacher
    <svg width="16" height="16" viewBox="0 0 16 16" fill="#555"><circle cx="8" cy="4.5" r="4"/><path d="M0 16c0-5 3.5-6.5 8-6.5s8 1.5 8 6.5z"/></svg>
  </div>
  <div class="search-btn">SEARCH</div>
</aside>

<aside class="help">
  <h3>How Can We<br>Help?</h3>
  <p>"Report an Issue" link mattis augue vehicula odio posuere, sit amet tempus lectus luctus.</p>
</aside>

<section class="newsletter">
  <h3>Newsletter Sign Up</h3>
  <div class="email">Email Address
    <svg width="19" height="15" viewBox="0 0 19 15"><rect width="19" height="15" rx="2" fill="#7d6bc2"/><path d="M1 2l8.5 6.5L18 2" fill="none" stroke="#fff" stroke-width="1.6"/></svg>
  </div>
</section>

<footer class="site-footer">
  <div class="footer-links">Home<span>|</span>Courses<span>|</span>Worksheets<span>|</span>Quizzes<span>|</span>Blog<span>|</span>Support</div>
  <div class="copyright">Copyright © 2019 &nbsp;Verdana Crest. &nbsp;All rights reserved.</div>
  <div class="social" style="left:866px;background:#3b5a9a" aria-label="Social link"></div>
  <div class="social" style="left:898px;background:#2aa3e0" aria-label="Social link"></div>
  <div class="social" style="left:932px;background:#cc2127" aria-label="Social link"></div>
  <div class="social" style="left:964px;background:#f57d00" aria-label="Social link"></div>
  <div class="social" style="left:996px;background:#e52d27" aria-label="Social link"></div>
  <div class="social" style="left:1029px;background:#6a8caf" aria-label="Social link"></div>
</footer>

</body>
</html>
```